Spring Detox sale graphics for social media

You MUST read the Brief in the WORD document and follow the instructions there. I want to create 10 social media graphics (new Instagram size 4:5 (1080 x 1350 pixels) focusing on our Mother’s Day Spring Detox Sale graphics, using any of the pics attached. Use the attached pics, NO RANDOM STOCK PHOTOGRAPHY. For the color scheme of the graphics, they should all be complementary to the product colors or feel like Spring time.

Target Market(s)

primarily women

Requirements
Must have
• the photos and text attached

```html
<!DOCTYPE html>
<html lang="en">
<head>
<meta charset="utf-8">
<title>Mother's Day Spring Detox Sale – Social Set</title>
<link href="https://fonts.googleapis.com/css2?family=Oswald:wght@200;300;500;700&family=Montserrat:wght@600;700&display=swap" rel="stylesheet">
<style>
:root{
  --board:#2b2b2b;
  --white:#ffffff;
  --ink:#2a2a2a;
  --red:#d62828;
  --red-soft:#fde3e3;
  --plum:#8a3d6b;
  --plum-soft:#f7eaf4;
  --blue:#2f4597;
  --blue-soft:#e6ebfb;
  --forest:#23473b;
  --mint:#e9fbf6;
  --sage:#4f8f72;
  --sage-soft:#bfe3d4;
  --sage-mid:#82c6a8;
  --orchid:#c0588f;
  --orchid-soft:#fde8f4;
  --lavender:#eef0fb;
  --cond:"Oswald", "Arial Narrow", sans-serif;
  --round:"Montserrat", "Helvetica", sans-serif;
}
*{margin:0;padding:0;box-sizing:border-box}
html,body{width:1200px;height:3119px;overflow:hidden;background:var(--board)}
.board{position:absolute;left:0;top:0;width:991px;height:2576px;transform:scale(1.21090);transform-origin:0 0}
.post{position:absolute;width:380px;height:475px;background:var(--white);overflow:hidden}
.col-a{left:108px}.col-b{left:508px}
.row-1{top:62px}.row-2{top:562px}.row-3{top:1062px}.row-4{top:1562px}.row-5{top:2062px}
.panel{position:absolute;border-radius:12px;border:1px solid rgba(0,0,0,.12)}
.band{position:absolute;left:0;right:0}
.t{position:absolute;font-family:var(--cond);line-height:.9;white-space:nowrap;letter-spacing:-.5px}
.bold{font-weight:700}
.thin{font-weight:200}
.mid{font-weight:500}
.center{left:0;right:0;text-align:center}
.ribbon{position:absolute;font-family:var(--round);font-weight:700;text-align:center;line-height:1;
  clip-path:polygon(0 0,100% 0,calc(100% - 14px) 50%,100% 100%,0 100%,14px 50%)}
.vertical{position:absolute;font-family:var(--cond);font-weight:700;writing-mode:vertical-rl;transform:rotate(180deg);line-height:.85;white-space:nowrap;letter-spacing:-.5px;overflow:hidden}
.photo{position:absolute;border-radius:8px 8px 0 0}
.bottles{position:absolute;border-radius:10px;background:linear-gradient(180deg,#fbfbfb 0%,#e9e9ee 70%,#d9d9e2 100%);display:flex;align-items:center;justify-content:space-around;padding:0 6px}
.bottles span{font-family:var(--round);font-weight:700;font-size:10px;color:var(--ink);background:var(--white);padding:3px 4px;border-radius:3px}
</style>
</head>
<body>
<main class="board">

  <section class="post col-a row-1">
    <div class="panel" style="left:16px;top:20px;width:347px;height:440px;background:var(--red-soft)"></div>
    <div class="band" style="top:422px;height:53px;background:var(--red)"></div>
    <div class="photo" role="img" aria-label="Smiling woman in a white crop top standing behind the supplement bottles" style="left:218px;top:96px;width:162px;height:379px;background:linear-gradient(180deg,#f3d9dc 0%,#e9e4e6 55%,#2d2d2d 100%)"></div>
    <div class="t bold" style="left:30px;top:44px;font-size:38px;color:var(--red)">Mother’s Day</div>
    <div class="t thin" style="left:28px;top:98px;font-size:62px;color:var(--ink)">SPRING</div>
    <div class="t bold" style="left:28px;top:154px;font-size:72px;color:var(--ink)">DETOX</div>
    <div class="ribbon" style="left:32px;top:248px;width:172px;height:32px;padding-top:5px;font-size:22px;background:var(--red);color:var(--white)">25% OFF</div>
    <div class="t mid" style="left:28px;top:288px;font-size:40px;color:var(--ink)">Everything!</div>
  </section>

  <section class="post col-b row-1">
    <div class="panel" style="left:16px;top:20px;width:348px;height:440px;background:var(--plum-soft)"></div>
    <div class="band" style="top:395px;height:80px;background:var(--plum)"></div>
    <div class="panel" style="left:35px;top:55px;width:137px;height:183px;background:var(--plum);border:none"></div>
    <div class="t bold" style="left:40px;top:70px;font-size:74px;color:var(--white)">25%</div>
    <div class="t bold" style="left:40px;top:142px;font-size:92px;color:var(--white)">OFF</div>
    <div class="t mid" style="left:180px;top:57px;font-size:30px;color:var(--ink)">MOTHER’S DAY</div>
    <div class="t thin" style="left:179px;top:88px;font-size:63px;color:var(--plum)">SPRING</div>
    <div class="t bold" style="left:179px;top:144px;font-size:66px;color:var(--ink)">DETOX</div>
    <div class="ribbon" style="left:180px;top:208px;width:165px;height:30px;padding-top:5px;font-size:22px;background:var(--plum);color:var(--white)">Sale</div>
    <div class="bottles" role="img" aria-label="Four supplement bottles: Blood Sugar Bloom, Hormone Bloom, Tummy Bloom, Liver Bloom" style="left:22px;top:255px;width:340px;height:200px;background:transparent">
      <span>Blood Sugar Bloom</span><span>Hormone Bloom</span><span>Tummy Bloom</span><span>Liver Bloom</span>
    </div>
  </section>

  <section class="post col-a row-2">
    <div class="panel" style="left:22px;top:20px;width:336px;height:300px;background:var(--blue-soft)"></div>
    <div class="band" style="top:265px;height:210px;background:var(--blue)"></div>
    <div class="t bold center" style="top:48px;font-size:74px;color:var(--blue)">25% OFF</div>
    <div class="t bold center" style="top:122px;font-size:36px;color:var(--ink)">ALL SUPPLEMENTS</div>
    <div class="t thin center" style="top:164px;font-size:102px;color:var(--blue)">SPRING</div>
    <div class="t bold center" style="top:272px;font-size:108px;color:var(--white)">DETOX</div>
    <div class="ribbon" style="left:60px;top:385px;width:262px;height:48px;padding-top:8px;font-size:34px;background:var(--white);color:var(--blue)">Sale!</div>
  </section>

  <section class="post col-b row-2">
    <div class="panel" style="left:22px;top:20px;width:336px;height:436px;background:var(--mint)"></div>
    <div class="t bold" style="left:34px;top:44px;font-size:76px;color:var(--forest)">25% OFF</div>
    <div class="panel" style="left:35px;top:120px;width:263px;height:200px;background:var(--forest);border:none"></div>
    <div class="t thin" style="left:50px;top:132px;font-size:92px;color:var(--white)">SPRING</div>
    <div class="t bold" style="left:50px;top:214px;font-size:102px;color:var(--white)">DETOX</div>
    <div class="ribbon" style="left:38px;top:326px;width:260px;height:42px;padding-top:7px;font-size:32px;background:var(--ink);color:var(--white)">Sale</div>
    <div class="t thin" style="left:35px;top:372px;font-size:62px;color:var(--ink)">Spring Reset</div>
    <div class="vertical" style="left:310px;top:48px;height:390px;font-size:56px;color:var(--forest)">SUMMER READY</div>
  </section>

  <section class="post col-a row-3">
    <div class="panel" style="left:22px;top:20px;width:336px;height:260px;background:var(--red-soft)"></div>
    <div class="band" style="top:210px;height:265px;background:var(--red)"></div>
    <div class="t bold center" style="top:38px;font-size:70px;color:var(--red)">25% OFF</div>
    <div class="t thin center" style="top:104px;font-size:58px;color:var(--ink)">EVERYTHING</div>
    <div class="t bold center" style="top:158px;font-size:48px;color:var(--red)">Mother’s Day</div>
    <div class="t thin center" style="top:224px;font-size:98px;color:var(--white)">SPRING</div>
    <div class="t bold center" style="top:308px;font-size:102px;color:var(--white)">DETOX</div>
    <div class="ribbon" style="left:66px;top:410px;width:250px;height:44px;padding-top:7px;font-size:34px;background:var(--ink);color:var(--white)">Sale</div>
  </section>

  <section class="post col-b row-3">
    <div class="panel" style="left:22px;top:20px;width:336px;height:436px;background:var(--orchid-soft)"></div>
    <div class="t bold center" style="top:40px;font-size:68px;color:var(--orchid)">25% OFF</div>
    <div class="t mid center" style="top:110px;font-size:44px;color:var(--ink)">MOTHER’S DAY</div>
    <div class="ribbon" style="left:66px;top:158px;width:250px;height:42px;padding-top:7px;font-size:32px;background:var(--orchid);color:var(--white)">Sale</div>
    <div class="band" style="top:240px;height:50px;left:22px;right:22px;background:#d98bb6"></div>
    <div class="bottles" role="img" aria-label="Four supplement bottles: Liver Bloom, Tummy Bloom, Hormone Bloom, Blood Sugar Bloom" style="left:32px;top:210px;width:316px;height:125px;background:transparent">
      <span>Liver Bloom</span><span>Tummy Bloom</span><span>Hormone Bloom</span><span>Blood Sugar Bloom</span>
    </div>
    <div class="t thin center" style="top:354px;font-size:36px;color:var(--ink)">FEEL AMAZING</div>
    <div class="t bold center" style="top:386px;font-size:58px;color:var(--orchid)">AGAIN!</div>
  </section>

  <section class="post col-a row-4">
    <div class="panel" style="left:22px;top:20px;width:336px;height:436px;background:var(--lavender)"></div>
    <div class="panel" style="left:22px;top:255px;width:336px;height:201px;background:var(--blue);border:none;border-radius:0 0 12px 12px"></div>
    <div class="t bold" style="left:37px;top:50px;font-size:64px;color:var(--blue)">25% OFF</div>
    <div class="t mid" style="left:37px;top:112px;font-size:40px;color:var(--ink)">MOTHER’S DAY</div>
    <div class="ribbon" style="left:38px;top:155px;width:216px;height:38px;padding-top:6px;font-size:30px;background:var(--blue);color:var(--white)">Sale</div>
    <div class="t thin" style="left:36px;top:200px;font-size:43px;color:var(--ink)">REFRESH YOUR</div>
    <div class="vertical" style="left:272px;top:48px;height:194px;font-size:80px;color:var(--ink)">BODY</div>
    <div class="bottles" role="img" aria-label="Four supplement bottles: Liver Bloom, Tummy Bloom, Hormone Bloom, Blood Sugar Bloom" style="left:30px;top:255px;width:320px;height:140px;background:transparent">
      <span>Liver Bloom</span><span>Tummy Bloom</span><span>Hormone Bloom</span><span>Blood Sugar Bloom</span>
    </div>
  </section>

  <section class="post col-b row-4">
    <div class="panel" style="left:22px;top:20px;width:336px;height:436px;background:linear-gradient(180deg,#e6f7ef 0%,var(--sage-soft) 100%)"></div>
    <div class="t bold" style="left:32px;top:48px;font-size:76px;color:var(--sage)">25% OFF</div>
    <div class="t thin" style="left:31px;top:116px;font-size:100px;color:var(--forest)">SPRING</div>
    <div class="t bold" style="left:31px;top:202px;font-size:106px;color:var(--forest)">DETOX</div>
    <div class="ribbon" style="left:34px;top:320px;width:262px;height:44px;padding-top:7px;font-size:34px;background:var(--sage-mid);color:var(--forest)">Sale</div>
    <div class="t thin" style="left:32px;top:374px;font-size:57px;color:var(--ink)">Spring Cleanse</div>
    <div class="vertical" style="left:310px;top:48px;height:385px;font-size:56px;color:var(--sage)">SUMMER GLOW</div>
  </section>

  <section class="post col-a row-5">
    <div class="panel" style="left:22px;top:20px;width:336px;height:436px;background:var(--red-soft)"></div>
    <div class="panel" style="left:22px;top:20px;width:266px;height:140px;background:var(--red);border:none"></div>
    <div class="bottles" role="img" aria-label="Four supplement bottles: Blood Sugar Bloom, Hormone Bloom, Tummy Bloom, Liver Bloom" style="left:30px;top:30px;width:250px;height:120px">
      <span>Blood Sugar</span><span>Hormone</span><span>Tummy</span><span>Liver</span>
    </div>
    <div class="t bold" style="left:54px;top:184px;font-size:64px;color:var(--red)">25% OFF</div>
    <div class="t mid" style="left:54px;top:244px;font-size:39px;color:var(--ink)">MOTHER’S DAY</div>
    <div class="ribbon" style="left:56px;top:285px;width:200px;height:36px;padding-top:6px;font-size:28px;background:var(--red);color:var(--white)">Sale</div>
    <div class="t thin" style="left:54px;top:326px;font-size:62px;color:var(--ink)">Detox This</div>
    <div class="t bold" style="left:54px;top:386px;font-size:66px;color:var(--ink)">SPRING</div>
    <div class="vertical" style="left:302px;top:30px;height:415px;font-size:50px;color:var(--red)">SHINE THIS SUMMER</div>
  </section>

  <section class="post col-b row-5">
    <div class="panel" style="left:22px;top:20px;width:336px;height:436px;background:linear-gradient(180deg,#fbeaf4 0%,var(--orchid-soft) 100%)"></div>
    <div class="panel" style="left:22px;top:20px;width:336px;height:140px;background:var(--plum);border:none"></div>
    <div class="t bold center" style="top:36px;font-size:72px;color:var(--white)">25% OFF</div>
    <div class="t bold center" style="top:108px;font-size:44px;color:var(--white)">MOTHER’S DAY</div>
    <div class="t center" style="top:172px;font-family:var(--round);font-weight:700;font-size:34px;color:var(--ink)">Sale</div>
    <div class="t thin center" style="top:214px;font-size:102px;color:var(--plum)">SPRING</div>
    <div class="t bold center" style="top:300px;font-size:108px;color:var(--ink)">DETOX</div>
    <div class="t center" style="top:410px;font-size:38px;color:var(--ink)"><span class="thin">for a </span><span class="mid" style="color:var(--plum)">Summer Body</span></div>
  </section>

</main>
</body>
</html>
```